Word Template Designs for Offensive Security Professional Services Report

We need a Microsoft Word Template designed for our Offensive Security professional services reports which includes the following services:

RedTeaming
Network Penetration Testing
Web Application Penetration Testing
Wireless Penetration Testing
Social Engineering

The templates should include the following:
Cover Page design with our Logo included
Executive Summary Page design
Detailed Findings Page design
Design for Last Page

Lastly, I would also like a template I can use for all of my Statements of Work

Requirements
Must have
• Beautiful Eye Catching HD pictures that represent my Offensive Security projects
The design should flow well with our logo

```html
<!DOCTYPE html>
<html lang="en">
<head>
<meta charset="utf-8">
<title>Scope of Work Template – Page Layouts</title>
<link href="https://fonts.googleapis.com/css2?family=Lato:wght@400;700;900&display=swap" rel="stylesheet">
<style>
:root{
  --backdrop:#5e5e5e;
  --paper:#ffffff;
  --ink:#1e1e1e;
  --body:#3a3a3a;
  --muted:#8a8a8a;
  --green:#4b8b2c;
  --rule:#c9c9c9;
  --navy:#0b1f3a;
  --teal:#1d5f78;
  --blue:#1d49a8;
}
*{box-sizing:border-box;margin:0;padding:0}
html,body{width:1200px;height:3599px;overflow:hidden}
body{background:var(--backdrop);font-family:"Lato",Arial,sans-serif;color:var(--body);position:relative}
.page{position:absolute;width:378px;height:534px;background:var(--paper);overflow:hidden}
.page-num{position:absolute;left:16px;bottom:14px;font-size:4.5px;color:var(--muted)}
.page-url{position:absolute;right:16px;bottom:14px;font-size:5.5px;color:var(--green)}
.brand{display:flex;flex-direction:column;align-items:center;gap:3px}
.brand-mark{width:40px;height:40px;border-radius:50%;background:#2b2b2b}
.brand-name{font-weight:700;color:#2b2b2b;font-size:11px}
.brand.small .brand-mark{width:24px;height:24px}
.brand.small .brand-name{font-size:7px}
.page-title{font-weight:900;font-size:17px;color:var(--ink);letter-spacing:.2px}
.page-title .accent,.sub .accent{color:var(--green)}
.sub{font-weight:900;font-size:9px;color:var(--ink);margin:8px 0 4px}
.sub.green{color:var(--green)}
.copy{font-size:4.7px;line-height:6.6px;margin-bottom:4px}
.list{font-size:4.7px;line-height:7px;padding-left:12px}
.list.indent{padding-left:26px}
.list.dots{list-style:disc}
.content{position:absolute;left:16px;right:16px;top:22px}
/* cover */
.cover-head{position:absolute;left:31px;top:103px;width:320px}
.cover-kicker{font-weight:900;font-size:12px;color:var(--green)}
.cover-title{font-weight:900;font-size:15px;line-height:18.5px;color:var(--ink);margin-top:2px}
.cover-for{font-weight:900;font-size:10.5px;color:var(--ink);margin-top:14px}
.cover-client{font-size:10.5px;color:var(--ink)}
.art{position:absolute;left:0;top:0;width:100%;height:100%}
.cover-by{position:absolute;left:31px;top:353px;color:#fff;font-size:6.2px;line-height:8px}
.cover-by strong{font-size:10px;font-weight:900;display:block;margin-bottom:2px}
.cover-by p{margin-bottom:5px}
.cover-url{position:absolute;left:31px;bottom:22px;color:#7fc35a;font-size:6.5px;font-weight:700;letter-spacing:.4px}
/* tables */
.rev-table{width:100%;border-collapse:collapse;font-size:5px;margin-top:10px}
.rev-table th{color:var(--green);font-weight:400;font-size:7px;border-bottom:1px solid var(--rule);padding:3px 0;text-align:center}
.rev-table td{text-align:center;padding:3px 0}
.toc{position:absolute;left:12px;right:26px;top:156px;list-style:none}
.toc li{display:flex;justify-content:space-between;font-size:4.8px;border-bottom:1px solid var(--rule);height:19px;align-items:flex-end;padding-bottom:3px}
.toc li.major{font-weight:900}
.services{display:grid;grid-template-columns:1fr 1fr;font-size:4.8px;line-height:8px;padding-left:8px}
.services span::before{content:"✓ ";color:var(--green)}
.checks{display:grid;grid-template-columns:1fr 1fr;font-size:4.7px;line-height:7.6px;padding-left:14px;margin:4px 0}
.checks span{display:flex;align-items:center;gap:6px}
.checks span::before{content:"";width:6px;height:6px;border-radius:50%;background:var(--green)}
.sign{position:absolute;left:180px;right:16px;bottom:22px;font-size:4.5px}
.sign div{border-bottom:1px solid var(--rule);height:22px;display:flex;align-items:flex-end}
.back-contact{position:absolute;left:0;right:0;top:152px;text-align:center;font-size:8px;color:var(--ink);line-height:12px}
.back-contact .ico{display:block;color:var(--green);font-size:7px}
.back-contact p{margin-bottom:10px}
</style>
</head>
<body>

<!-- Row 1 -->
<section class="page" style="left:201px;top:82px">
  <div class="brand" style="position:absolute;left:0;right:0;top:20px"><div class="brand-mark"></div><div class="brand-name">Breachpoint Labs</div></div>
  <div class="cover-head">
    <div class="cover-kicker">SCOPE OF WORK :</div>
    <div class="cover-title">External, Internal Network,<br>Wireless and Web Application Penetration<br>Testing Engagement</div>
    <div class="cover-for">PREPARED FOR :</div>
    <div class="cover-client">[Client Name]</div>
  </div>
  <svg class="art" viewBox="0 0 378 534" role="img" aria-label="Photo of a glowing circuit board with a shield and padlock symbol">
    <defs><linearGradient id="coverGrad" x1="0" y1="0" x2="1" y2="1"><stop offset="0" stop-color="#0f3b57"/><stop offset=".5" stop-color="#0a2438"/><stop offset="1" stop-color="#071624"/></linearGradient></defs>
    <polygon points="0,315 378,168 378,178 0,325" fill="var(--green)"/>
    <polygon points="0,331 378,184 378,534 0,534" fill="url(#coverGrad)"/>
  </svg>
  <div class="cover-by">
    <strong>PREPARED BY :</strong>
    <p>Daniel Harlow, CISSP, OSCE, OSCP<br>[Company Name], LLC</p>
    <p>2210 Ridge Park Dr Suite 4<br>Austin Texas 78701<br>www.breachpointlabs.com</p>
    <p>daniel.harlow@breachpointlabs.com<br>Office 1800.555.0142<br>Mobile: 210.555.0187<br>August 2, 2018</p>
  </div>
  <div class="cover-url">www.breachpointlabs.com</div>
</section>

<section class="page" style="left:616px;top:82px">
  <div class="content" style="top:26px">
    <h1 class="page-title"><span class="accent">SCOPE</span> APPROVAL</h1>
    <h2 class="sub"><span class="accent">CLIENT ACTIVITY</span> CHECKLIST</h2>
    <ul class="list dots">
      <li>Provide access to client's facilities, as required.</li>
      <li>Provide access to client's existing policy documentation.</li>
      <li>Provide access to client's intranet portal.</li>
      <li>Provide workspace and Internet connections for [Company Name] consultants for any on-site activities.</li>
      <li>Provide access to client's technical staff (network administrators, security officers, database administrators, etc.) who can answer questions about the current environment.</li>
      <li>Provide access to the following information, documentation (as required):
        <ul class="list" style="padding-left:8px;list-style:circle"><li>Policies, Standards, Guidelines, Procedures relevant to this work.</li><li>Any other reasonable information deemed necessary for the successful completion of this engagement.</li><li>Facilitate communication with Telco, ISP or other connected sites as needed.</li></ul></li>
      <li>Provide a single point of contact that will be responsible for:
        <ul class="list" style="padding-left:8px;list-style:circle"><li>Arrangements and clearances from client management</li><li>Delivery of necessary information to [Company Name] to complete the project</li><li>Approvals to scope of work changes (including acceptance of additional billing)</li><li>Interfaces with client project management or change management as needed</li><li>Approve project delivery based on defined success criteria.</li></ul></li>
    </ul>
    <h2 class="sub green">ACKNOWLEDGEMENTS</h2>
    <p class="copy">[Company Name] will work with the client during the course of this project to ensure that each of the phases and tasks are complete as described herein and that [Company Name] completes all of the deliverables identified in this document.</p>
    <p class="copy">Any additional deliverables and/or changes to the project task list or phases are considered changes in the scope of work. Such changes require a new scope of work to be issued and signed. Changes that exceed twenty percent (20%) of the total original project cost will require a purchase order.</p>
    <p class="copy">The solution described in this document is based on [Company Name] current understanding of the client's environment, business, and technical requirements. Any changes could affect the project cost and/or schedule.</p>
    <p class="copy">A purchase order must be issued to [Company Name] before the project can be scheduled and resources assigned.</p>
    <p class="copy">I acknowledge receipt and acceptance of this project scope of work.</p>
  </div>
  <div class="sign"><div>Client Signature</div><div>Date</div><div>Client Name</div></div>
  <div class="page-num">Page 16</div>
</section>

<!-- Row 2 -->
<section class="page" style="left:201px;top:662px">
  <div class="content" style="top:20px">
    <h1 class="page-title" style="text-align:center;font-size:15px"><span class="accent">DOCUMENT REVISION</span> CONTROL</h1>
    <table class="rev-table">
      <thead><tr><th>Revision Number</th><th>Revision</th><th>Revision Date</th></tr></thead>
      <tbody><tr><td>1.0</td><td>Initial</td><td>8/2/18</td></tr></tbody>
    </table>
  </div>
  <div class="page-num">Page 2</div>
</section>

<section class="page" style="left:616px;top:662px">
  <div class="brand small" style="position:absolute;right:22px;top:16px"><div class="brand-mark"></div><div class="brand-name">Breachpoint Labs</div></div>
  <h1 class="page-title" style="position:absolute;left:12px;top:112px"><span class="accent">TABLE OF</span> CONTENTS</h1>
  <ul class="toc">
    <li class="major"><span>TABLE OF CONTENTS</span><span>3</span></li>
    <li class="major"><span>PROPOSAL SUMMARY</span><span>4</span></li>
    <li><span>ENGAGEMENT OVERVIEW</span><span>4</span></li>
    <li><span>Phase One: External Network Penetration Testing</span><span>4</span></li>
    <li><span>Phase Two: Internal Network Penetration Testing</span><span>4</span></li>
    <li><span>Phase Three: Wireless Penetration Testing</span><span>5</span></li>
    <li><span>Phase Four: Targeted Web Application Penetration Testing</span><span>5</span></li>
    <li><span>ENGAGEMENT DELIVERABLES</span><span>6</span></li>
    <li><span>PHASE SPECIFIC TASKS</span><span>7</span></li>
    <li><span>Phase One: External Network Penetration Testing</span><span>7</span></li>
    <li><span>Phase Two: Internal Network Penetration Testing</span><span>9</span></li>
    <li><span>Phase Three: Wireless Penetration Testing</span><span>11</span></li>
    <li><span>Phase Four: Targeted Web Application Penetration Testing</span><span>12</span></li>
    <li class="major"><span>ABOUT [COMPANY NAME]</span><span>15</span></li>
    <li><span>CONSULTANT PROFILE</span><span>15</span></li>
    <li class="major"><span>SCOPE APPROVAL</span><span>16</span></li>
    <li><span>CLIENT ACTIVITY CHECKLIST</span><span>16</span></li>
    <li><span>ACKNOWLEDGEMENTS</span><span>16</span></li>
  </ul>
  <div class="page-num">Page 3</div>
</section>

<!-- Row 3 -->
<section class="page" style="left:201px;top:1231px">
  <div class="content" style="top:26px">
    <h1 class="page-title"><span class="accent">PROPOSAL</span> SUMMARY</h1>
    <p class="copy">[Company Name] is proud to present this multi-phase Scope of Work to [Client Name] to meet their Penetration Testing Requirements. [Company Name] LLC's security consultants have expert knowledge in Network Security and Web Applications, Security Controls, process and procedures, best practices, vulnerabilities and countermeasures. Our security consultants will perform the penetration testing presented in this Scope of Work.</p>
    <h2 class="sub green">ENGAGEMENT <span style="color:var(--ink)">OVERVIEW</span></h2>
    <p class="copy">Based on the information provided, [Company Name] understands that [Client Name] objectives are to have [Company Name] LLC provide penetration testing, ethical hacking and risk management services to [Client Name] to help ensure that the systems are working in a safe secure manner and ensuring the proper preservation of all data's Confidentiality, Integrity, and Availability (CIA).</p>
    <p class="copy">From [Company Name]'s understanding, [Client Name] has requested that the penetration testing be performed from a grey box perspective to determine the exposed vulnerabilities of the networks, applications and wireless implementations.</p>
    <p class="copy" style="color:var(--green)">In response to these requirements, [Company Name] will perform the following services :</p>
    <div class="services"><span>External Network Penetration Testing</span><span>Internal Network Penetration Testing</span><span>Wireless Network Penetration Testing</span><span>Targeted Web Application Penetration Testing</span></div>
    <h2 class="sub">PHASE ONE: <span class="accent">EXTERNAL NETWORK PENETRATION TESTING</span></h2>
    <p class="copy">[Company Name] will conduct a Network Penetration Testing assessment of the external network, aka the Internet presence, to help identify existing vulnerabilities and their associated risks. [Company Name] will discover and identify hosts belonging to [Client Name] external network, identify vulnerabilities and exploit vulnerabilities identified during the ethical hacking process. After a system is compromised, the vulnerabilities and any applicable exploits will be documented in a detailed, repeatable process.</p>
    <p class="copy">[Company Name] will conduct this work remotely while performing the Network Penetration Testing assessment in collaboration with [Client Name] personnel. After the assessment is complete, [Company Name] will develop a formal report that will include the items described in the Final Report Summary.</p>
    <h2 class="sub">PHASE TWO: <span class="accent">INTERNAL NETWORK PENETRATION TESTING</span></h2>
    <p class="copy">[Company Name] will conduct a penetration test of the [Client Name] internal network, aka their private LAN. [Company Name] will exploit vulnerabilities identified during the vulnerability identification process. After a system is compromised, the vulnerabilities and any applicable exploits will be documented in a detailed, repeatable process.</p>
    <p class="copy">[Company Name] will conduct this work onsite initially and remotely after deploying [Company Name]'s internal network attack server. The Network Penetration Testing will be conducted in collaboration with [Client Name] personnel. After the assessment is complete, [Company Name] will develop a formal report that will include the items described in the Final Report Summary.</p>
    <p class="copy"><strong>Note :</strong> The attack server's purpose is to facilitate internal network penetration testing efforts from a remote offsite location. This will help emulate an attacker who has gained access to the internal network and is outside of the organization.</p>
  </div>
  <div class="page-num">Page 4</div><div class="page-url">www.breachpointlabs.com</div>
</section>

<section class="page" style="left:616px;top:1231px">
  <div class="content" style="top:18px">
    <h2 class="sub" style="margin-top:0">PHASE THREE: <span class="accent">WIRELESS PENETRATION TESTING</span></h2>
    <p class="copy">[Company Name] will assess [Client Name] guest and production wireless networks. During testing, [Company Name] will attempt to gain access to hosts belonging to [Client Name]' internal network presence and wireless controllers. [Company Name] will exploit vulnerabilities identified during the vulnerability identification process. After a system or information is compromised, [Company Name] will gather appropriate evidence for proof of information or system compromise.</p>
    <p class="copy">[Company Name] will conduct this work on-site while performing the assessment in collaboration with [Client Name]. After the assessment is complete, [Company Name] will develop a formal report that will include the items described in the Final Report Summary.</p>
    <h2 class="sub">PHASE FOUR: <span class="accent">TARGETED WEB APPLICATION PENETRATION TESTING</span></h2>
    <p class="copy">[Company Name] will conduct a Targeted Web Application Penetration Testing assessment of the target web application and supporting services as an unauthenticated and authenticated user to determine the vulnerabilities that are accessible to an attacker.</p>
    <p class="copy"><span style="color:var(--green)">Unauthorized/Unauthenticated</span> – An Unauthenticated Assessment of your web application gives a realistic view of what an attacker with a simple Internet connection and no privileges would be able to access, find, and possibly exploit. This type of assessment tests the strengths of your application's authentication mechanisms and any other vulnerability associated with the application.</p>
    <p class="copy"><span style="color:var(--green)">Authorized/Authenticated</span> – An authenticated Assessment of your web application gives a realistic view of what an attacker with basic and administrative privileges would be able to access, find, and possibly exploit. This type of assessment tests the strengths of your applications to withstand attacks by authorized users who have valid credentials to authenticate to the application.</p>
    <p class="copy">Additional testing may include the following :</p>
    <div class="checks">
      <span>Information Leakage</span><span>OS Command Injection</span>
      <span>Session Management</span><span>Local and Remote File Inclusion</span>
      <span>Default Configurations</span><span>Cross Site Request Forgery</span>
      <span>Authentication abuse</span><span>Application and Business Logic Flaws</span>
      <span>Client-Side Cache</span><span>Proper Input Validation</span>
      <span>Authorization exploitation</span><span>Privilege Escalation Opportunities</span>
      <span>SQL injection, (backend database enumeration)</span><span>Client-Side Code</span>
      <span></span><span>Server-Side Input Validation</span>
    </div>
    <p class="copy">[Company Name] follows a well-developed and proven methodology to assess the security of web-based applications as defined in the specific tasks in the next section. After the assessment is complete, [Company Name] will develop a formal report that will include the items described in the Final Report Summary.</p>
    <h2 class="sub green">ENGAGEMENT <span style="color:var(--ink)">DELIVERABLES</span></h2>
    <p class="copy">[Company Name] will provide the following Deliverables to [Client Name]:</p>
    <ul class="list dots" style="color:var(--body)">
      <li>Weekly Status Updates if applicable</li>
      <li>Final Report and Presentation delivered at the end of the engagement</li>
      <li>Onsite Q&amp;A session with our consultants to discuss the process, findings, and recommendations, and answer questions related to the engagement.</li>
    </ul>
  </div>
  <div class="page-num">Page 5</div><div class="page-url">www.breachpointlabs.com</div>
</section>

<!-- Row 4 -->
<section class="page" style="left:201px;top:1799px">
  <div class="content" style="top:22px">
    <h1 class="page-title"><span class="accent">PHASE SPECIFIC</span> TASKS</h1>
    <p class="copy" style="margin-top:4px">This engagement consists of four phases which break down into the following tasks and milestones.</p>
    <h2 class="sub">PHASE ONE: <span class="accent">EXTERNAL NETWORK PENETRATION TESTING</span></h2>
    <div class="list" style="padding-left:8px">
      <div>Duration: [Timeframe]</div><div>Consultant Presence: 100% Remote</div><div>Client Time Commitment: 1 - 2 staff hours</div>
      <div>The goal of this phase is to conduct a Penetration Test of [Client Name] Internet Presence.</div>
      <div>This consulting engagement consists of four stages:</div>
      <div><strong>Stage 1:</strong> Project/Phase Kickoff</div>
    </div>
    <ul class="list indent dots"><li>Identify Stakeholders and responsible parties</li><li>Establish Timelines</li><li>Identify sources of required information</li></ul>
    <div class="list" style="padding-left:8px">
      <div><strong>Stage 2:</strong> External Network Ethical Hacking</div>
      <div>1. Determine and validate specified IP addresses to be tested based on information supplied by the client.</div>
      <div>2. Gather public information about the organization such as but not limited to:</div>
    </div>
    <ul class="list indent dots"><li>Employee names, phone numbers and email addresses</li><li>Computer account naming conventions</li><li>Domain registry information</li><li>Help Desk information and support procedures</li></ul>
    <div class="list" style="padding-left:8px"><div>3. Gather specific information such as:</div></div>
    <ul class="list indent dots"><li>Information from DNS servers about organizational systems</li><li>Information derived from email transfers</li><li>Trace route information to organization systems</li></ul>
    <div class="list" style="padding-left:8px"><div>4. Use port scanners to determine the following information:</div></div>
    <ul class="list indent dots"><li>Ports and services available on the information systems</li><li>Web, Mail, DNS, Firewall, Routers, Switches address information</li><li>Operating system, and application versioning information</li></ul>
    <div class="list" style="padding-left:8px">
      <div>5. Use service specific tools to gather additional information from server about user configurations</div>
      <div>7. Conduct a vulnerability scan of exposed system and services and create a prioritized list of exploits for use.</div>
      <div>8. Check for common administrative misconfigurations such as:</div>
    </div>
    <ul class="list indent dots"><li>Common and default system service accounts</li><li>Default usernames and passwords</li><li>Default community strings (SNMP)</li><li>Mail relay allowed on SMTP servers</li></ul>
    <div class="list" style="padding-left:8px"><div>9. Perform password-based attacks on:</div></div>
    <ul class="list indent dots"><li>Servers (telnet, FTP, SMB VNC, MSRDP, basic authentication etc)</li><li>Routers (telnet, SSH and community strings)</li></ul>
    <div class="list" style="padding-left:8px"><div><strong>Stage 3:</strong> Early Warning Notification</div></div>
    <ul class="list indent dots"><li>Review Vulnerability, Threat Vectors, Exploits and Possible Countermeasures.</li></ul>
    <div class="list" style="padding-left:8px"><div><strong>Stage 4:</strong> Data Analysis and Draft Report</div></div>
    <ul class="list indent dots"><li>Data Analysis</li><li>Draft Report Creation</li></ul>
  </div>
  <div class="page-num">Page 6</div><div class="page-url">www.breachpointlabs.com</div>
</section>

<section class="page" style="left:616px;top:1799px">
  <div class="content" style="top:20px">
    <h2 class="sub green" style="margin-top:0">CLIENT <span style="color:var(--ink)">OBLIGATIONS</span></h2>
    <p class="copy">Working Sessions will be conducted during both on-site meeting and via [Company Name] provided web-based collaboration / teleconferences and will require extensive interaction with the client, as detailed by meeting schedule below. The client will be required to provide access to IT managers, IT Staff in order to define the basic data sets and elements.</p>
    <h2 class="sub green">MEETING <span style="color:var(--ink)">SCHEDULES</span></h2>
    <ul class="list dots" style="padding-left:8px"><li><u>Phase One kick-off</u> (30 minutes) to establish a timeline and review client requirements.</li><li>Final Report will be presented at the end of the assessment.</li></ul>
  </div>
  <div class="page-num">Page 7</div><div class="page-url">www.breachpointlabs.com</div>
</section>

<!-- Row 5 -->
<section class="page" style="left:201px;top:2373px">
  <div class="content" style="top:22px">
    <h2 class="sub" style="margin-top:0">PHASE TWO: <span class="accent">INTERNAL NETWORK PENETRATION TESTING</span></h2>
    <div class="list" style="padding-left:0">
      <div>Timeline: [Timeframe]</div><div>Consultant Presence: 25% Onsite, 75% Remote</div><div>Client Time Commitment: 3 - 4 staff hours</div>
      <div>The goal of this phase is to conduct an ethical hacking exercise on [Client Name]' internal network in a collaborative fashion.</div>
      <div>This phase of the consulting engagement consists of four stages:</div>
      <div><strong>Stage 1:</strong> Project/Phase Kickoff</div>
    </div>
    <ul class="list indent dots"><li>Identify Stakeholders and responsible parties</li><li>Establish Timelines</li><li>Identify sources of required information</li></ul>
    <div class="list" style="padding-left:0">
      <div><strong>Stage 2:</strong> Internal Network Ethical Hacking</div>
      <div>1. Determine and validate specified IP addresses to be tested based on information supplied by the client.</div>
      <div>2. Gather public information about the organization such as but not limited to:</div>
    </div>
    <ul class="list indent dots"><li>Employee names, phone numbers and email addresses</li><li>Computer account naming conventions</li><li>Domain registry information</li><li>Help Desk information and support procedures</li></ul>
    <div class="list" style="padding-left:0"><div>3. Gather specific information such as:</div></div>
    <ul class="list indent dots"><li>Information from DNS servers about organizational systems</li><li>Information derived from email transfers</li><li>Trace route information to organization systems</li></ul>
    <div class="list" style="padding-left:0"><div>4. Use port scanners to determine the following information:</div></div>
    <ul class="list indent dots"><li>Ports and services available on the information systems</li><li>Web, Mail, DNS, Firewall, Routers, Switches address information</li><li>Operating system, and application versioning information</li></ul>
    <div class="list" style="padding-left:0">
      <div>5. Use service specific tools to gather additional information from server about user configurations</div>
      <div>6. Conduct a vulnerability scan of exposed system and services and create a prioritized list of exploits for use.</div>
      <div>7. Check for common administrative misconfigurations such as:</div>
    </div>
    <ul class="list indent dots"><li>Common and default system service accounts</li><li>Default usernames and passwords</li><li>Default community strings (SNMP)</li><li>Mail relay allowed on SMTP servers</li></ul>
    <div class="list" style="padding-left:0"><div>8. Perform password-based attacks on:</div></div>
    <ul class="list indent dots"><li>Servers (telnet, FTP, SMB VNC, MSRDP, basic authentication etc)</li><li>Routers (telnet, SSH and community strings)</li></ul>
    <div class="list" style="padding-left:0"><div><strong>Stage 3:</strong> Data Analysis and Draft Report</div></div>
    <ul class="list indent dots"><li>Data Analysis</li><li>Draft Report Creation</li></ul>
  </div>
  <div class="page-num">Page 8</div><div class="page-url">www.breachpointlabs.com</div>
</section>

<section class="page" style="left:624px;top:2373px">
  <div class="content" style="top:20px">
    <h2 class="sub green" style="margin-top:0">CLIENT <span style="color:var(--ink)">OBLIGATIONS</span></h2>
    <p class="copy">Working Sessions will be conducted during both on-site meeting and via [Company Name] provided web-based collaboration / teleconferences and will require extensive interaction with the client, as detailed by meeting schedule below. The client will be required to provide access to IT managers, IT Staff in order to define the basic data sets and elements.</p>
    <h2 class="sub green">MEETING <span style="color:var(--ink)">SCHEDULES</span></h2>
    <ul class="list dots" style="padding-left:8px"><li><u>Phase Two kick-off</u> (30 minutes) to establish a timeline and review client requirements.</li><li>Final Report will be presented at the end of the assessment.</li></ul>
  </div>
  <div class="page-num">Page 9</div><div class="page-url">www.breachpointlabs.com</div>
</section>

<!-- Row 6: back page -->
<section class="page" style="left:425px;top:2960px">
  <div class="brand" style="position:absolute;left:0;right:0;top:74px"><div class="brand-mark"></div><div class="brand-name" style="font-size:13px">Breachpoint Labs</div></div>
  <div class="back-contact">
    <p><span class="ico">☎</span>1-800-555-0142</p>
    <p><span class="ico">✉</span>info@example.com</p>
    <p><span class="ico">⌂</span>www.breachpointlabs.com</p>
  </div>
  <svg class="art" viewBox="0 0 378 534" role="img" aria-label="Photo of a blue hexagon network pattern with glowing padlock icons">
    <defs><linearGradient id="backGrad" x1="0" y1="0" x2="0" y2="1"><stop offset="0" stop-color="#2f63c4"/><stop offset=".6" stop-color="var(--blue)"/><stop offset="1" stop-color="#0c2360"/></linearGradient></defs>
    <polygon points="0,383 378,285 378,295 0,393" fill="var(--green)"/>
    <polygon points="0,399 378,301 378,534 0,534" fill="url(#backGrad)"/>
  </svg>
</section>

</body>
</html>
```